We need a complete design for our construction company KELTO CONSTRUCTION based in Auckland New Zealand, we need a logo, website, business card, vehicle design etc..
We are a mid to high-end construction company who work mostly on residential projects and some commercial.

What we want to see in the design;
Professional,
Architectural,
Simple,
Alternative,

We want the design to communicate professionalism, high quality wormanship and and quality service.

Target Market(s)

People looking for a quality building/ construction company

Industry/Entity Type

Construction Company

Contact Information for Business Card

KELTO CONSTRUCTION.co.nz
Lino Verasek
lino@keltoconstruction.example.nz
021 5807 462

Logo Text

KELTO CONSTRUCTION

Number of Pages Required

5+ page

Font styles to use
Sans Serif

Colors

Designer to choose colors to be used in the design.

Requirements
Must have
• Must appear high end, professional, quality, be simple, easy to use, give security to potential clients
Nice to have
• high-quality photos of our recent projects
• about us page
• blog page
• contact us page
• high quality content
Should not have
• should not be hard to use and have too much going on.

```html
<!DOCTYPE html>
<html lang="en">
<head>
<meta charset="utf-8">
<title>Kelto Construction</title>
<link rel="stylesheet" href="https://fonts.googleapis.com/css2?family=Jost:wght@400;500&family=Open+Sans:wght@400;600&display=swap">
<style>
:root{
  --ink:#222;
  --dark:#2a2a2a;
  --darker:#262626;
  --panel:#efefef;
  --white:#fff;
  --muted:#444;
  --line:#3a3a3a;
}
*{box-sizing:border-box;margin:0;padding:0}
html,body{width:1200px;height:2308px;overflow:hidden}
body{position:relative;background:var(--white);font-family:"Open Sans",Arial,sans-serif;color:var(--ink)}
.abs{position:absolute}
.site-header{left:0;top:0;width:1200px;height:95px;background:var(--dark)}
.brand{left:129px;top:18px;font-family:"Jost",sans-serif;font-size:45px;font-weight:500;color:var(--white);letter-spacing:.3px}
.main-nav{right:134px;top:39px;display:flex;gap:26px;font-family:"Jost",sans-serif;font-size:14px;color:var(--white);text-transform:uppercase}
.main-nav .current{text-decoration:underline;text-underline-offset:4px}
.hero{left:0;top:95px;width:1200px;height:520px;background:linear-gradient(100deg,#c9c7b3 0%,#6f86a7 28%,#2f4b86 52%,#6d7fa7 68%,#3b3950 100%)}
.hero-caption{left:132px;top:277px;width:360px;height:158px;background:rgba(255,255,255,.35);padding:10px 20px}
.hero-caption h1{font-size:34px;font-weight:600;line-height:40px;color:#2b2b2b}
.call-btn{display:inline-flex;align-items:center;gap:8px;margin-top:12px;background:#222;color:var(--white);font-size:16px;font-weight:600;padding:7px 14px}
.slide-arrow{width:22px;height:32px}
.welcome-title{left:0;top:688px;width:1200px;text-align:center;font-family:"Jost",sans-serif;font-size:31px;font-weight:400}
.welcome-text{left:138px;top:738px;width:924px;text-align:center;font-size:12.5px;line-height:21px;color:var(--muted)}
.service-btn{height:79px;width:443px;border:2px solid #333;display:flex;align-items:center;justify-content:center;gap:12px;font-family:"Jost",sans-serif;font-size:24px;text-transform:uppercase;letter-spacing:.5px}
.projects{left:0;top:1020px;width:1200px;height:632px;background:var(--darker)}
.section-title{width:1200px;text-align:center;font-family:"Jost",sans-serif;font-size:31px}
.projects .section-title{color:var(--white)}
.project-tile{width:217px;height:191px}
.blog-card{width:440px;height:120px;background:var(--panel);display:flex}
.blog-thumb{width:152px;height:120px;flex:none}
.blog-body{padding:14px 16px}
.blog-body h3{font-size:15.5px;font-weight:400;line-height:21px;color:#222}
.blog-meta{margin-top:14px;font-size:10px;color:#333}
.blog-more{font-size:10px;font-weight:600;margin-top:3px}
.more-btn{left:555px;top:1937px;width:90px;height:34px;border:1px solid #ccc;font-size:11px;color:#555;display:flex;align-items:center;justify-content:center}
.cta{left:0;top:2051px;width:1200px;height:160px;background:var(--panel)}
.cta-text{top:38px;width:1200px;text-align:center;font-family:"Jost",sans-serif;font-size:22px}
.cta-btn{left:532px;top:77px;width:136px;height:41px;background:var(--dark);color:var(--white);display:flex;align-items:center;justify-content:center;gap:10px;font-size:16px;font-weight:600}
.site-footer{left:0;top:2211px;width:1200px;height:97px;background:var(--dark);color:#ccc;font-size:11px}
.footer-links{left:132px;top:27px;display:flex;gap:10px}
.copyright{left:132px;top:54px}
.social{width:14px;height:14px;border-radius:50%;background:#bbb;top:43px}
</style>
</head>
<body>

<header class="site-header abs">
  <div class="brand abs">Kelto Construction</div>
  <nav class="main-nav abs">
    <span class="current">Home</span><span>About us</span><span>Projects</span><span>Blog</span><span>Contact us</span>
  </nav>
</header>

<section class="hero abs" role="img" aria-label="Modern glass house with a wooden deck and infinity pool overlooking mountains at dusk">
  <div class="hero-caption abs">
    <h1>Aliquam consectetur orci molestie</h1>
    <div class="call-btn">
      <svg width="14" height="14" viewBox="0 0 24 24"><path fill="#fff" d="M6.6 10.8a15 15 0 0 0 6.6 6.6l2.2-2.2a1 1 0 0 1 1-.25 11.4 11.4 0 0 0 3.6.57 1 1 0 0 1 1 1V20a1 1 0 0 1-1 1A17 17 0 0 1 3 4a1 1 0 0 1 1-1h3.5a1 1 0 0 1 1 1c0 1.25.2 2.45.57 3.57a1 1 0 0 1-.25 1z"/></svg>
      Call us on : 555 204 7781
    </div>
  </div>
  <svg class="slide-arrow abs" style="left:43px;top:246px" viewBox="0 0 22 32"><path d="M16 4 6 16l10 12" fill="none" stroke="#fff" stroke-width="4"/></svg>
  <svg class="slide-arrow abs" style="left:1134px;top:246px" viewBox="0 0 22 32"><path d="M6 4l10 12L6 28" fill="none" stroke="#fff" stroke-width="4"/></svg>
</section>

<h2 class="welcome-title abs">Welcome to Kelto Construction</h2>
<p class="welcome-text abs">Vestibulum condimentum, risus ut posuere cursus, velit justo accumsan sem, lobortis aliquet metus dui eu libero. Pellentesque a imperdiet dolor, et auctor est. Fusce sollicitudin lorem et luctus volutpat. Proin placerat dapibus gravida. In tristique tristique nulla eget hendrerit. Maecenas vel tortor accumsan quam varius imperdiet vel eget elit. Aenean facilisis tincidunt lectus, id dictum nisi luctus eget. Vivamus efficitur ex condimentum, malesuada eros eget, feugiat nibh. Sed tellus ex, imperdiet eget gravida sit amet, volutpat eget turpis. In nec ultricies est. Etiam mattis augue vehicula odio posuere.</p>

<div class="service-btn abs" style="left:132px;top:861px">
  <svg width="18" height="16" viewBox="0 0 18 16"><path d="M9 1 1 8h2v7h4v-4h4v4h4V8h2z" fill="#333"/></svg>
  Residential Construction
</div>
<div class="service-btn abs" style="left:623px;top:861px">
  <svg width="14" height="18" viewBox="0 0 14 18"><path d="M1 1h12v16H8v-3H6v3H1z" fill="#333"/><path d="M4 4h2v2H4zm4 0h2v2H8zM4 8h2v2H4zm4 0h2v2H8z" fill="#fff"/></svg>
  Commercial Construction
</div>

<section class="projects abs">
  <h2 class="section-title abs" style="top:74px">Our Projects</h2>
  <div class="project-tile abs" style="left:132px;top:137px;background:linear-gradient(180deg,#3a5f93,#7a5a4a)" role="img" aria-label="Lit hillside home by the water at dusk"></div>
  <div class="project-tile abs" style="left:371px;top:137px;background:linear-gradient(180deg,#e8e8e8,#4a4a4a 55%,#3e86b8)" role="img" aria-label="Modern house with swimming pool"></div>
  <div class="project-tile abs" style="left:611px;top:137px;background:linear-gradient(180deg,#4f88cc,#eaeaea 55%,#8a4a40)" role="img" aria-label="White cubic modern villa"></div>
  <div class="project-tile abs" style="left:851px;top:137px;background:linear-gradient(180deg,#6fa2d8,#d8c18a 50%,#6a6a5a)" role="img" aria-label="Apartment building with balconies"></div>
  <div class="project-tile abs" style="left:132px;top:354px;background:linear-gradient(180deg,#2d5fb0,#c9b49a 55%,#a56458)" role="img" aria-label="Mediterranean home with palm trees and paved drive"></div>
  <div class="project-tile abs" style="left:371px;top:354px;background:linear-gradient(180deg,#1f4f9e,#9aa3b2 55%,#4b7a3a)" role="img" aria-label="Two storey family house with garage"></div>
  <div class="project-tile abs" style="left:611px;top:354px;background:linear-gradient(180deg,#5d7fa8,#bfa08a 55%,#3d7fa2)" role="img" aria-label="Villa with pool and deck at sunset"></div>
  <div class="project-tile abs" style="left:851px;top:354px;background:linear-gradient(180deg,#3a4f86,#5a5e6a 55%,#4a6a3a)" role="img" aria-label="Large grey home with lit windows at dusk"></div>
  <svg class="slide-arrow abs" style="left:43px;top:324px" viewBox="0 0 22 32"><path d="M16 4 6 16l10 12" fill="none" stroke="#fff" stroke-width="4"/></svg>
  <svg class="slide-arrow abs" style="left:1134px;top:324px" viewBox="0 0 22 32"><path d="M6 4l10 12L6 28" fill="none" stroke="#fff" stroke-width="4"/></svg>
</section>

<h2 class="section-title abs" style="top:1725px">Blog</h2>
<article class="blog-card abs" style="left:132px;top:1785px">
  <div class="blog-thumb" style="background:linear-gradient(160deg,#5f7f63,#3a6f86 50%,#b9a98a)" role="img" aria-label="Aerial view of a waterfront housing development"></div>
  <div class="blog-body">
    <h3>Vestibulum condimentum, risus ut posuere cursus, velit accumsan</h3>
    <div class="blog-meta">By Mara Ellis &nbsp;|&nbsp; 19 Mar, 2018 &nbsp;|&nbsp; 5 Comments</div>
    <div class="blog-more">Read more</div>
  </div>
</article>
<article class="blog-card abs" style="left:628px;top:1785px">
  <div class="blog-thumb" style="background:linear-gradient(160deg,#dfe6ee,#b05c45 50%,#3a3a3a)" role="img" aria-label="Couple standing in front of a modern brick home"></div>
  <div class="blog-body">
    <h3>Pellentesque a imperdiet dolor, et auctor est. Fusce sollicitudin.</h3>
    <div class="blog-meta">By Mara Ellis &nbsp;|&nbsp; 19 Mar, 2018 &nbsp;|&nbsp; 5 Comments</div>
    <div class="blog-more">Read more</div>
  </div>
</article>
<div class="more-btn abs">Read more</div>

<section class="cta abs">
  <p class="cta-text abs">Maecenas vel tortor accumsan quam varius imperdiet vel eget elit</p>
  <div class="cta-btn abs">
    <svg width="16" height="12" viewBox="0 0 16 12"><rect width="16" height="12" fill="#fff"/><path d="M0 0l8 6 8-6" fill="none" stroke="#2a2a2a" stroke-width="1.6"/></svg>
    Contact Us
  </div>
</section>

<footer class="site-footer abs">
  <div class="footer-links abs"><span>Home</span><span>|</span><span>About us</span><span>|</span><span>Projects</span><span>|</span><span>Blog</span><span>|</span><span>Contact us</span></div>
  <div class="copyright abs">Copyright © 2018 &nbsp;Kelto Construction. &nbsp;All rights reserved.</div>
  <span class="social abs" style="left:1014px"></span>
  <span class="social abs" style="left:1050px"></span>
</footer>

</body>
</html>
```